Halvor Grading and Septic needs a flyer to submit to contractors to offer our services

I need a sleek profession one page full color high gloss document showcasing our services to give to Mobile Home Companies and contractors that need our services.

Target Market(s)

Home Builders. Mobile Home Salesmen. People Building new homes.

Industry/Entity Type

Construction

Font styles to use
Serif
Sans Serif

Requirements
Must have
• Phone Number. Email address. Logo. Services offered: Mobile Home Pads, Meter Pole Placement and Connection, Waterline Connection, On Site Septic System Installs
Should not have
• Jokes, Nothing trying to be cute

```html
<!DOCTYPE html>
<html lang="en">
<head>
<meta charset="utf-8">
<title>Halvor Grading and Septic – Services Flyer</title>
<link rel="stylesheet" href="https://fonts.googleapis.com/css2?family=Barlow+Condensed:ital,wght@0,400;0,500;0,700;1,400;1,700&display=swap">
<style>
  :root {
    --page: #ffffff;
    --sheet: #ddeaf6;
    --brand-blue: #1a5189;
    --ink: #1e1e1e;
    --accent-red: #d3202b;
    --photo-earth: #b98c5a;
    --photo-sky: #8fb3dd;
    --photo-grass: #7c8f4c;
  }
  * { box-sizing: border-box; margin: 0; padding: 0; }
  html, body {
    width: 1200px; height: 1000px; overflow: hidden;
    background: var(--page);
    font-family: "Barlow Condensed", "Arial Narrow", sans-serif;
  }
  .flyer {
    position: absolute; left: 341px; top: 133px;
    width: 518px; height: 733px;
    background: var(--sheet);
  }
  .photo { position: absolute; }
  .photo--trench { left: 31px; top: 32px; width: 147px; height: 196px;
    background: linear-gradient(180deg, #6e8a4a 0%, var(--photo-earth) 30%, #a97a48 100%); }
  .photo--pad { left: 185px; top: 32px; width: 148px; height: 110px;
    background: linear-gradient(180deg, #c9b98f 0%, #a8643d 55%, #9a4e2c 100%); }
  .photo--sprinkler { left: 340px; top: 32px; width: 147px; height: 196px;
    background: linear-gradient(180deg, #9dbde3 0%, #c7cfd2 35%, #8a6a4c 60%, #6e553e 100%); }
  .photo--home { left: 185px; top: 150px; width: 148px; height: 196px;
    background: linear-gradient(180deg, var(--photo-sky) 0%, #d8dde3 40%, #b8a483 65%, #c6b391 100%); }
  .photo--tank { left: 31px; top: 235px; width: 147px; height: 111px;
    background: linear-gradient(180deg, #2f6fc6 0%, #7aa5dc 55%, var(--photo-grass) 72%, #6b8740 100%); }
  .photo--excavator { left: 340px; top: 235px; width: 147px; height: 111px;
    background: linear-gradient(180deg, #3a78c8 0%, #6f8e4e 30%, #c89e6c 60%, #d1ab7e 100%); }

  .headline {
    position: absolute; left: 31px; top: 378px;
    font-weight: 700; font-style: italic;
    font-size: 42px; line-height: 46px; color: var(--ink);
    letter-spacing: 0.2px;
  }
  .headline .word-blue { color: var(--brand-blue); }
  .headline .word-red { color: var(--accent-red); }

  .region-banner {
    position: absolute; left: 31px; top: 531px; width: 219px; height: 30px;
    background: var(--brand-blue); color: #fff;
    font-size: 19px; line-height: 30px; text-align: center; font-weight: 400;
  }

  .services { position: absolute; left: 267px; top: 384px; width: 225px; list-style: none; }
  .service { margin-bottom: 9px; }
  .service__title { font-size: 17px; font-weight: 500; color: var(--brand-blue); line-height: 20px; }
  .service__desc { font-size: 10.5px; font-style: italic; color: var(--ink); line-height: 13px; margin-top: 2px; }
  .service--tall .service__desc { width: 180px; }

  .brand {
    position: absolute; left: 31px; top: 612px; width: 228px;
    display: flex; align-items: center; gap: 8px;
  }
  .brand__mark { width: 14px; height: 14px; border-radius: 50%; background: var(--brand-blue); flex: none; }
  .brand__name {
    font-size: 28px; line-height: 30px; font-weight: 700; color: var(--brand-blue);
  }

  .counties {
    position: absolute; left: 340px; top: 596px; width: 147px;
    display: flex; flex-direction: column; gap: 4px;
  }
  .counties__row { display: flex; gap: 3px; }
  .county {
    flex: 1 1 auto; height: 14px; background: var(--brand-blue); color: #fff;
    font-size: 11.5px; line-height: 14px; text-align: center;
  }

  .contact { position: absolute; left: 340px; top: 655px; width: 160px; }
  .contact__phone {
    display: flex; align-items: center; gap: 6px;
    color: var(--accent-red); font-size: 14px; font-style: italic; font-weight: 500; height: 18px;
  }
  .contact__line {
    display: flex; align-items: center; gap: 5px; margin-top: 3px; padding-left: 2px;
    color: var(--brand-blue); font-size: 9.5px; font-style: italic;
  }
  .contact svg { flex: none; fill: var(--brand-blue); }
</style>
</head>
<body>
<main class="flyer">
  <div class="photo photo--trench" role="img" aria-label="Excavator digging a septic trench beside a mobile home"></div>
  <div class="photo photo--pad" role="img" aria-label="Graded red-dirt pad with septic lids in front of a mobile home"></div>
  <div class="photo photo--sprinkler" role="img" aria-label="Aerobic septic sprinkler spraying over a graded field"></div>
  <div class="photo photo--home" role="img" aria-label="New mobile home set on a freshly graded pad"></div>
  <div class="photo photo--tank" role="img" aria-label="Concrete septic tank being lowered by a boom truck"></div>
  <div class="photo photo--excavator" role="img" aria-label="Excavator backfilling around an installed septic tank"></div>

  <h1 class="headline">
    <span class="word-blue">Expert</span> Mobile<br>
    Home Services<br>
    You Can <span class="word-red">Trust</span>
  </h1>

  <p class="region-banner">Excavating Services in East Texas</p>

  <ul class="services">
    <li class="service">
      <h2 class="service__title">Mobile Home Pads</h2>
      <p class="service__desc">Durable and stable pad installations for mobile homes.</p>
    </li>
    <li class="service service--tall">
      <h2 class="service__title">Meter Pole Placement and Connection</h2>
      <p class="service__desc">Professional meter pole placement and reliable electrical connections.</p>
    </li>
    <li class="service">
      <h2 class="service__title">Waterline Connection</h2>
      <p class="service__desc">Efficient and secure waterline connections for new homes.</p>
    </li>
    <li class="service">
      <h2 class="service__title">On Site Septic System Installs</h2>
      <p class="service__desc">Comprehensive septic system installations for your property.</p>
    </li>
  </ul>

  <div class="brand">
    <span class="brand__mark"></span>
    <p class="brand__name">Halvor Grading<br>and Septic</p>
  </div>

  <div class="counties" aria-label="Counties served">
    <div class="counties__row"><span class="county">Ellis</span><span class="county">Anderson</span><span class="county">Navarro</span></div>
    <div class="counties__row"><span class="county">Henderson</span><span class="county">Kaufman</span><span class="county">Van Zandt</span></div>
    <div class="counties__row"><span class="county">Smith</span><span class="county">Cherokee</span><span class="county">Limestone</span></div>
  </div>

  <div class="contact">
    <p class="contact__phone">
      <svg width="13" height="13" viewBox="0 0 24 24" aria-hidden="true"><path d="M6.6 10.8a15.1 15.1 0 0 0 6.6 6.6l2.2-2.2a1 1 0 0 1 1-.25 11.4 11.4 0 0 0 3.6.57 1 1 0 0 1 1 1V20a1 1 0 0 1-1 1A17 17 0 0 1 3 4a1 1 0 0 1 1-1h3.5a1 1 0 0 1 1 1c0 1.25.2 2.45.57 3.57a1 1 0 0 1-.25 1z"/></svg>
      (903) 555-0148
    </p>
    <p class="contact__line">
      <svg width="8" height="7" viewBox="0 0 24 18" aria-hidden="true"><path d="M0 0h24v2L12 10 0 2z M0 5l12 8 12-8v13H0z"/></svg>
      office@halvorgradingseptic.com
    </p>
    <p class="contact__line">
      <svg width="7" height="7" viewBox="0 0 24 24" aria-hidden="true"><circle cx="12" cy="12" r="11"/></svg>
      halvorgradingseptic.com
    </p>
  </div>
</main>
</body>
</html>
```